Website for Ashcombe Tube Drift

Require a website for a river float in the City of Edmonton. Located on North Saskatchewan River. Will need to be a coded website with incorporated booking system through Fare Harbor software.

Pages include
Home
Pricing
About
FAQ
Contact

Ashcombe Tube Drift is an activity based business that will have customers floating down the North Saskatchewan river in Edmonton AB. The site will have all information needed and a full reservation system. The project was launched to provide people in the Edmonton area a favorite summer activity.

Here are similar websites to reference what our business will be doing and what we are looking for.

mossbankfloatco.com
quillpointpaddles.com

Target Market(s)

Families, Groups, Individuals, Anyone who wants to explore the river

Industry/Entity Type

Activities based business/ Outdoor recreational/ River Float

Coding

Coded - Design and coding required

Number of Pages Required

5+ page

Colors
0054AA
0677BA
7BADD7
CADEEF
E8F1F8
F0912C
F2A743
F7CA91
FBE8D2
FDF5EE

```html
<!DOCTYPE html>
<html lang="en">
<head>
<meta charset="utf-8">
<title>Ashcombe Tube Drift</title>
<link href="https://fonts.googleapis.com/css2?family=Rubik:wght@400;500;700&family=Arimo:wght@400;700&display=swap" rel="stylesheet">
<style>
:root{
  --blue:#0054AA;
  --mid:#0677BA;
  --sky:#4EC4E8;
  --pale:#E8F1F8;
  --light:#CADEEF;
  --navy:#0C2D6B;
  --ink:#2A2A2A;
  --grey:#555;
  --white:#fff;
}
*{box-sizing:border-box;margin:0;padding:0}
html,body{width:1200px;height:3885px;overflow:hidden}
body{position:relative;background:var(--white);font-family:"Arimo",Arial,sans-serif;color:var(--ink)}
.abs{position:absolute}
.rubik{font-family:"Rubik",Arial,sans-serif}
.btn{position:absolute;display:flex;align-items:center;justify-content:center;font-family:"Rubik",Arial,sans-serif;font-weight:500;border-radius:40px;text-transform:uppercase}
.btn-outline{border:2px solid var(--blue);color:var(--blue);background:var(--white)}

/* header */
.site-header{position:absolute;left:0;top:0;width:1200px;height:113px;background:var(--white);border-top:2px solid var(--blue);z-index:3}
.brand-badge{position:absolute;left:114px;top:-10px;width:166px;height:166px;border-radius:50%;background:var(--white);display:flex;align-items:center;justify-content:center;text-align:center;z-index:4;box-shadow:0 4px 10px rgba(0,0,0,.08)}
.brand-badge span{font-family:"Rubik",Arial,sans-serif;font-weight:700;font-size:19px;line-height:1.15;color:var(--blue);width:120px;margin-top:30px}
.main-nav{position:absolute;top:50px;left:648px;font-family:"Rubik",Arial,sans-serif;font-weight:500;font-size:15px;color:#222}
.main-nav a{position:absolute;white-space:nowrap;text-decoration:none;color:inherit}
.main-nav a.active{color:var(--blue)}

/* hero */
.hero{position:absolute;left:0;top:113px;width:1200px;height:671px}
.hero-photo{position:absolute;inset:0;background:linear-gradient(180deg,#cfe2f4 0%,#e6eef5 22%,#b9b7ae 42%,#7f8a6e 58%,#5a7a3c 70%,#6c8d86 82%,#4e6b4a 100%)}
.hero-title{position:absolute;top:72px;width:1200px;text-align:center;font-family:"Rubik",Arial,sans-serif;font-weight:500;font-size:43px;color:var(--blue)}
.hero-sub{position:absolute;top:134px;width:1200px;text-align:center;font-family:"Rubik",Arial,sans-serif;font-size:21px;color:#222}
.hero .btn{left:507px;top:184px;width:186px;height:54px;font-size:19px;background:rgba(255,255,255,.35)}
.slide-arrow{position:absolute;top:317px;width:36px;height:36px}

/* pricing */
.pricing-photo{position:absolute;left:112px;top:843px;width:485px;height:656px;border-radius:0 70px 0 70px;background:linear-gradient(180deg,#3f6a34 0%,#6f8e5b 35%,#d9e1e3 55%,#eef2f3 68%,#8a8a86 85%,#5d5d5a 100%)}
.price-title{position:absolute;left:644px;top:850px;font-family:"Rubik",Arial,sans-serif;font-size:30px;color:#333}
.price-amount{position:absolute;left:641px;top:900px;font-family:"Rubik",Arial,sans-serif;font-weight:500;font-size:46px;color:var(--blue)}
.price-unit{position:absolute;left:725px;top:929px;font-family:"Rubik",Arial,sans-serif;font-size:14px;color:#333}
.price-lead{position:absolute;left:644px;top:972px;width:430px;font-size:14px;line-height:27px;color:#444}
.inclusions{position:absolute;left:642px;top:1033px;list-style:none;font-size:15.5px;color:#333}
.inclusions li{height:31.7px;display:flex;align-items:center;gap:18px}
.group-box{position:absolute;left:500px;top:1328px;width:589px;height:147px;background:var(--sky)}
.group-box h3{position:absolute;left:33px;top:47px;font-family:"Rubik",Arial,sans-serif;font-weight:500;font-size:24px;color:var(--white)}
.group-box p{position:absolute;left:32px;top:84px;font-size:13.5px;color:var(--white)}
.group-box .btn{left:370px;top:52px;width:180px;height:48px;border:2px solid var(--white);color:var(--white);font-size:17px}

/* about */
.about{position:absolute;left:0;top:1565px;width:1200px;height:597px;background:linear-gradient(100deg,#4fb3d9 0%,#3d95c8 35%,#1f6fb6 60%,#1c64ae 100%)}
.about h2{position:absolute;left:112px;top:42px;font-family:"Rubik",Arial,sans-serif;font-size:42px;font-weight:400;color:var(--white)}
.rule{position:absolute;height:3px;width:42px;background:var(--white)}
.about-copy{position:absolute;left:112px;top:118px;width:469px;font-size:13.6px;line-height:28.4px;color:var(--white);text-align:justify}
.about-copy p+p{margin-top:28px}
.about .btn{left:113px;top:499px;width:175px;height:54px;background:var(--blue);color:var(--white);font-size:18px}
.about-emblem{position:absolute;left:636px;top:100px;width:483px;height:393px;display:flex;align-items:center;justify-content:center}
.about-emblem .disc{width:390px;height:390px;border-radius:50%;background:var(--sky);border:14px solid var(--navy);display:flex;align-items:center;justify-content:center;text-align:center}
.about-emblem span{font-family:"Rubik",Arial,sans-serif;font-weight:700;font-size:38px;line-height:1.15;color:var(--white);width:260px}

/* faq */
.faq{position:absolute;left:0;top:2162px;width:1200px;height:718px;background:linear-gradient(180deg,#f6f9fc 0%,#eef3f7 45%,#e6eef0 70%,#f4f8f6 100%)}
.faq h2{position:absolute;top:53px;width:1200px;text-align:center;font-family:"Rubik",Arial,sans-serif;font-weight:400;font-size:39px;color:var(--blue)}
.faq .rule{left:579px;top:108px;background:var(--blue)}
.faq-item{position:absolute;left:276px;width:648px;height:54px;border:2px solid #dde3ea;border-radius:28px;background:rgba(255,255,255,.85);display:flex;align-items:center;padding-left:20px;font-family:"Rubik",Arial,sans-serif;font-size:15.5px;color:#333}
.faq-item b{font-weight:500;font-size:23px;color:var(--blue);margin-right:8px}
.faq-answer{position:absolute;left:327px;top:217px;width:570px;font-size:13.5px;line-height:26px;color:#666}

/* contact */
.contact h2{position:absolute;left:110px;top:2985px;font-family:"Rubik",Arial,sans-serif;font-weight:400;font-size:39px;color:var(--blue)}
.contact-sub{position:absolute;left:111px;top:3059px;font-family:"Rubik",Arial,sans-serif;font-size:17px;color:#555}
.contact-row{position:absolute;left:112px;display:flex;align-items:center;gap:16px}
.contact-row .icon{width:50px;height:50px;border-radius:50%;border:2px solid var(--blue);display:flex;align-items:center;justify-content:center}
.contact-row div{font-family:"Rubik",Arial,sans-serif;font-size:14.5px;line-height:20px;color:#333}
.social{position:absolute;width:42px;height:42px;border-radius:50%;border:1.5px solid #999}
.map{position:absolute;left:562px;top:2948px;width:527px;height:502px;border:4px solid #e6e9ee;border-radius:0 60px 0 60px;background:linear-gradient(180deg,#8fb0ef 0%,#8fb0ef 14%,#cfe7d3 18%,#cfe7d3 55%,#f2f4f4 62%,#eef1ef 100%)}

/* footer */
.site-footer{position:absolute;left:0;top:3513px;width:1200px;height:372px;background:var(--navy);color:var(--white)}
.footer-brand{position:absolute;left:130px;top:36px;display:flex;align-items:center;gap:12px}
.footer-brand .dot{width:60px;height:60px;border-radius:50%;background:var(--sky)}
.footer-brand span{font-family:"Rubik",Arial,sans-serif;font-weight:700;font-size:27px;line-height:1.1;color:var(--white);width:170px}
.footer-info{position:absolute;left:130px;top:244px;font-family:"Rubik",Arial,sans-serif;font-size:14.5px;line-height:26px}
.site-footer .social{border-color:var(--white)}
.days-badge{position:absolute;left:497px;top:60px;width:220px;height:128px;border-radius:10px;background:rgba(255,255,255,.12)}
.subscribe{position:absolute;left:443px;top:222px;width:344px;height:46px;border:1.5px solid var(--white);border-radius:24px;display:flex;align-items:center;justify-content:space-between;padding:0 20px 0 22px;font-family:"Rubik",Arial,sans-serif;font-size:14px}
.copyright{position:absolute;top:296px;width:1286px;text-align:center;font-family:"Rubik",Arial,sans-serif;font-size:14.5px}
.footer-nav{position:absolute;left:910px;top:68px;list-style:none;font-family:"Rubik",Arial,sans-serif;font-size:14.5px}
.footer-nav li{height:36px;display:flex;align-items:center;gap:12px}
</style>
</head>
<body>

<header class="site-header">
  <div class="brand-badge"><span>Ashcombe Tube Drift</span></div>
  <nav class="main-nav">
    <a class="active" style="left:0">HOME</a>
    <a style="left:90px">PRICING</a>
    <a style="left:197px">ABOUT</a>
    <a style="left:295px">FAQ</a>
    <a style="left:370px">CONTACT</a>
  </nav>
</header>

<section class="hero">
  <div class="hero-photo" role="img" aria-label="Downtown Edmonton skyline above the North Saskatchewan River with a bridge and green riverbank"></div>
  <h1 class="hero-title">ASHCOMBE TUBE DRIFT</h1>
  <p class="hero-sub">FLOAT THE NORTH SASKATCHEWAN THROUGH DOWNTOWN EDMONTON</p>
  <a class="btn btn-outline">Book Now</a>
  <svg class="slide-arrow" style="left:66px" viewBox="0 0 36 36"><circle cx="18" cy="18" r="16" fill="none" stroke="#333" stroke-width="1.5"/><path d="M21 11l-7 7 7 7" fill="none" stroke="#333" stroke-width="2"/></svg>
  <svg class="slide-arrow" style="left:1095px" viewBox="0 0 36 36"><circle cx="18" cy="18" r="16" fill="none" stroke="#333" stroke-width="1.5"/><path d="M15 11l7 7-7 7" fill="none" stroke="#333" stroke-width="2"/></svg>
</section>

<section class="pricing">
  <div class="pricing-photo" role="img" aria-label="Paddler in a red kayak running whitewater rapids below a forested bank"></div>
  <h2 class="price-title">TUBE AND SHUTTLE</h2>
  <div class="price-amount">$30</div>
  <div class="price-unit">/PERSON</div>
  <a class="btn btn-outline" style="left:799px;top:905px;width:146px;height:48px;font-size:16px">Book Now</a>
  <p class="price-lead">We keep our pricing simple and include everything you need :<br>Premium comfort float tube with backrest and cup holder</p>
  <ul class="inclusions">
    <li><svg width="16" height="14" viewBox="0 0 16 14"><path d="M1.5 7.5l4.5 4.5 8.5-10" fill="none" stroke="#0054AA" stroke-width="3"/></svg>Lifejacket</li>
    <li><svg width="16" height="14" viewBox="0 0 16 14"><path d="M1.5 7.5l4.5 4.5 8.5-10" fill="none" stroke="#0054AA" stroke-width="3"/></svg>Paddle</li>
    <li><svg width="16" height="14" viewBox="0 0 16 14"><path d="M1.5 7.5l4.5 4.5 8.5-10" fill="none" stroke="#0054AA" stroke-width="3"/></svg>Round trip shuttle service</li>
    <li><svg width="16" height="14" viewBox="0 0 16 14"><path d="M1.5 7.5l4.5 4.5 8.5-10" fill="none" stroke="#0054AA" stroke-width="3"/></svg>Safety training</li>
    <li><svg width="16" height="14" viewBox="0 0 16 14"><path d="M1.5 7.5l4.5 4.5 8.5-10" fill="none" stroke="#0054AA" stroke-width="3"/></svg>Staff assistance</li>
    <li><svg width="16" height="14" viewBox="0 0 16 14"><path d="M1.5 7.5l4.5 4.5 8.5-10" fill="none" stroke="#0054AA" stroke-width="3"/></svg>Parking</li>
    <li><svg width="16" height="14" viewBox="0 0 16 14"><path d="M1.5 7.5l4.5 4.5 8.5-10" fill="none" stroke="#0054AA" stroke-width="3"/></svg>Unlimited Fun!</li>
  </ul>
  <a class="btn btn-outline" style="left:644px;top:1262px;width:148px;height:48px;font-size:16px">Book Now</a>
  <div class="group-box">
    <h3>GROUP OF 10 OR MORE?</h3>
    <p>*does not include taxes or fees</p>
    <a class="btn">Contact Us</a>
  </div>
</section>

<section class="about" role="img" aria-label="Blue tinted river and forest backdrop">
  <h2>ABOUT US</h2>
  <div class="rule" style="left:112px;top:100px"></div>
  <div class="about-copy">
    <p>Float the North Saskatchewan through downtown Edmonton Ashcombe Tube Drift's Best Summer Activity We provide the lifejacket, paddle, river tube and shuttle service. You just have to show up. Ashcombe Tube Drift was launched to provide people in the Edmonton area a favorite summer</p>
    <p>activity. Nothing is better on a hot summer day, than spending it on the river and seeing Edmonton from a new perspective. Our home base and meeting spot is at Cedar Landing (Map Link), by the Glasshouse Conservatory. This is where you will check in, and board the shuttle. The shuttle will take all floaters up river to Willowbend Boat Launch, where your tube will be waiting. Once on the river, you can sit back, relax, explore and enjoy the view. Once you complete the float, and arrive back a close second. Don't miss out on Edmonton's best summer activity.</p>
  </div>
  <a class="btn">Book Now</a>
  <div class="about-emblem"><div class="disc"><span>Ashcombe Tube Drift</span></div></div>
</section>

<section class="faq">
  <h2>OUR FAQ'S</h2>
  <div class="rule"></div>
  <div class="faq-item" style="top:145px"><b>Q.</b>How do I reserve my float?</div>
  <p class="faq-answer">We highly recommend booking online, as we do sell out. BOOK NOW Floats can also be reserved on-site at Cedar Landing, on a first come first serve basis.</p>
  <div class="faq-item" style="top:294px"><b>Q.</b>What safety information should I know?</div>
  <div class="faq-item" style="top:361px"><b>Q.</b>What is included?</div>
  <div class="faq-item" style="top:430px"><b>Q.</b>What should I bring?</div>
  <div class="faq-item" style="top:498px"><b>Q.</b>Where are you located?</div>
  <div class="faq-item" style="top:564px"><b>Q.</b>What time should I arrive?</div>
</section>

<section class="contact">
  <h2>CONTACT US</h2>
  <p class="contact-sub">We'd love to hear from you!</p>
  <div class="contact-row" style="top:3112px">
    <span class="icon"><svg width="18" height="18" viewBox="0 0 24 24"><path d="M6.6 10.8a15 15 0 006.6 6.6l2.2-2.2a1 1 0 011-.25 11.4 11.4 0 003.6.57 1 1 0 011 1V20a1 1 0 01-1 1A17 17 0 013 4a1 1 0 011-1h3.5a1 1 0 011 1 11.4 11.4 0 00.57 3.6 1 1 0 01-.25 1z" fill="#0054AA"/></svg></span>
    <div>Phone<br>780 555 0142</div>
  </div>
  <div class="contact-row" style="top:3184px">
    <span class="icon"><svg width="18" height="14" viewBox="0 0 18 14"><rect x="1" y="1" width="16" height="12" rx="1.5" fill="none" stroke="#0054AA" stroke-width="1.6"/><path d="M1.5 2l7.5 6 7.5-6" fill="none" stroke="#0054AA" stroke-width="1.6"/></svg></span>
    <div>Email<br>info@ashcombetubedrift.com</div>
  </div>
  <div class="contact-row" style="top:3255px">
    <span class="icon"><svg width="14" height="18" viewBox="0 0 14 18"><path d="M7 17s6-6.3 6-10A6 6 0 001 7c0 3.7 6 10 6 10z" fill="#0054AA"/><circle cx="7" cy="7" r="2.2" fill="#fff"/></svg></span>
    <div>Address<br>4120 Ferrier Ave NW, Edmonton, AB</div>
  </div>
  <span class="social" style="left:113px;top:3333px"></span>
  <span class="social" style="left:163px;top:3333px"></span>
  <span class="social" style="left:213px;top:3333px"></span>
  <div class="map" role="img" aria-label="Street map of the river valley showing the meeting point near the conservatory"></div>
</section>

<footer class="site-footer">
  <div class="footer-brand"><span class="dot"></span><span>Ashcombe Tube Drift</span></div>
  <div class="footer-info">EMAIL: info@ashcombetubedrift.com<br>LOCATION: Cedar Landing</div>
  <span class="social" style="left:164px;top:308px"></span>
  <span class="social" style="left:214px;top:308px"></span>
  <span class="social" style="left:264px;top:308px"></span>
  <div class="days-badge" role="img" aria-label="Open 7 days a week lettering with a circular arrow"></div>
  <div class="subscribe"><span>Enter Your Email</span><svg width="16" height="16" viewBox="0 0 16 16"><path d="M1 7.5L15 1 9.5 15 7.5 9z" fill="none" stroke="#fff" stroke-width="1.4" stroke-linejoin="round"/><path d="M7.5 9L15 1" stroke="#fff" stroke-width="1.4"/></svg></div>
  <p class="copyright">© Copyrights 2022.All Rights Reserved.</p>
  <ul class="footer-nav">
    <li><svg width="9" height="9" viewBox="0 0 9 9"><path d="M1 1l3.5 3.5L1 8M4.5 1L8 4.5 4.5 8" fill="none" stroke="#fff" stroke-width="1.3"/></svg>HOME</li>
    <li><svg width="9" height="9" viewBox="0 0 9 9"><path d="M1 1l3.5 3.5L1 8M4.5 1L8 4.5 4.5 8" fill="none" stroke="#fff" stroke-width="1.3"/></svg>PRICING</li>
    <li><svg width="9" height="9" viewBox="0 0 9 9"><path d="M1 1l3.5 3.5L1 8M4.5 1L8 4.5 4.5 8" fill="none" stroke="#fff" stroke-width="1.3"/></svg>ABOUT</li>
    <li><svg width="9" height="9" viewBox="0 0 9 9"><path d="M1 1l3.5 3.5L1 8M4.5 1L8 4.5 4.5 8" fill="none" stroke="#fff" stroke-width="1.3"/></svg>FAQ</li>
    <li><svg width="9" height="9" viewBox="0 0 9 9"><path d="M1 1l3.5 3.5L1 8M4.5 1L8 4.5 4.5 8" fill="none" stroke="#fff" stroke-width="1.3"/></svg>CONTACT</li>
  </ul>
</footer>

</body>
</html>
```